Bluefinch Painting needs a Website

We need a website built for a Painting company I own, we mainly do residential painting, but don't want to be limited to that.

Need to have estimate request form.
Need pic's of past projects

I like the look of the website for http://www.harbor-brushworks.com
& "Westlake Home inspections"

My logo that was designed here on ArtHatch on the front page

I would like one of the houses I downloaded as part of the background
of the front page.

Target Market(s)

Home owners

Industry/Entity Type

Painting

Number of Pages Required

1 page

Font styles to use
Serif

Requirements
Must have
• Estimate request form for home owners to fill out -
• Name:
• Phone Number:
• Address:
• E-mail:
• Painting project description:
• And my info to:
• My phone number: (555) 318-7046
• My web address bluefinchpainting.example
Nice to have
• My logo that was designed here on ArtHatch

```html
<!DOCTYPE html>
<html lang="en">
<head>
<meta charset="utf-8">
<title>Bluefinch Painting</title>
<link href="https://fonts.googleapis.com/css2?family=Roboto+Slab:wght@400;500&family=Arimo:wght@400;700&display=swap" rel="stylesheet">
<style>
:root{
  --blue:#1e7cc8;
  --blue-dark:#1766a8;
  --black:#111;
  --footer:#191919;
  --text:#333;
  --muted:#555;
  --line:#bbb;
  --white:#fff;
}
*{box-sizing:border-box;margin:0;padding:0}
html,body{width:930px;height:1200px;overflow:hidden;background:#fff}
body{font-family:"Arimo",Arial,sans-serif;color:var(--text)}
.page{position:relative;width:930px;height:1200px;overflow:hidden}
.abs{position:absolute}
.serif{font-family:"Roboto Slab",Georgia,serif}

/* header */
.brand{left:124px;top:14px;display:flex;align-items:center;gap:8px}
.brand-mark{width:30px;height:30px;background:var(--blue)}
.brand-name{font-family:"Roboto Slab",Georgia,serif;font-size:22px;line-height:1;color:var(--black);letter-spacing:1px}
.trailer{left:503px;top:8px;width:151px;height:70px;background:linear-gradient(#f4f4f4,#d8d8d8);border:1px solid #ccc}
.estimate-btn{left:680px;top:3px;width:116px;height:22px;background:var(--blue);color:#fff;font-size:12px;text-align:center;line-height:22px}
.call{left:683px;top:40px;display:flex;gap:6px;align-items:center}
.call small{display:block;font-size:10px;color:#333}
.call strong{display:block;font-size:15px;font-weight:400;color:#222}

/* nav */
.nav{left:0;top:78px;width:930px;height:32px;background:var(--blue);display:flex;padding-left:125px}
.nav a{font-family:"Roboto Slab",Georgia,serif;font-size:11.5px;color:#fff;text-decoration:none;height:32px;line-height:32px;text-align:center;border-right:1px solid rgba(255,255,255,.35)}
.nav a.active{background:var(--black);font-weight:500}
.nav a:last-child{border-right:none}

/* hero */
.hero{left:0;top:110px;width:930px;height:306px;background:linear-gradient(160deg,#bdb9ac 0%,#a9a18a 22%,#d8ad3c 40%,#e7c44a 70%,#d9b23e 100%)}
.hero-arrow{width:30px;height:30px;border-radius:50%;background:#1b1b1b;border:2px solid rgba(120,120,120,.6);display:flex;align-items:center;justify-content:center}
.hero-copy{left:598px;top:238px;width:200px;text-align:center}
.hero-brand{font-family:"Roboto Slab",Georgia,serif;font-size:17px;color:var(--blue);letter-spacing:1px;display:flex;align-items:center;justify-content:center;gap:6px}
.hero-brand i{width:20px;height:20px;background:var(--blue);display:block}
.hero-tag{margin-top:16px;font-family:"Roboto Slab",Georgia,serif;font-size:17px;line-height:24px;color:#111}

/* welcome */
.welcome{left:0;top:416px;width:930px;height:168px;background:var(--blue);color:#fff;text-align:center}
.welcome h1{font-family:"Roboto Slab",Georgia,serif;font-weight:400;font-size:17px;margin-top:22px}
.welcome p{width:660px;margin:14px auto 0;font-size:9.6px;line-height:17px}
.read-dark{display:inline-block;background:var(--black);color:#fff;font-size:10px;padding:0 7px;height:18px;line-height:18px}

/* columns */
.col-title{font-family:"Roboto Slab",Georgia,serif;font-size:16px;color:#222;font-weight:400}
.photo{border:3px solid #ddd;outline:1px solid #bbb}
.col-text{font-size:9.6px;line-height:14.5px;color:#333;width:208px}
.inquiry-rule{left:608px;top:626px;width:203px;border-top:1px dashed #aaa}
.field{left:609px;width:198px;height:20px;border:1px solid #bbb;border-radius:2px;font-size:8.5px;font-style:italic;color:#666;padding:4px 8px}
.submit{left:614px;top:819px;width:60px;height:18px;background:var(--black);color:#fff;font-size:10px;font-weight:700;text-align:center;line-height:18px}

/* gallery */
.divider{left:133px;top:866px;width:672px;height:2px;background:linear-gradient(90deg,transparent,#ddd 20%,#ddd 80%,transparent)}
.gallery-icon{left:137px;top:885px;width:40px;height:40px;border-radius:50%;border:1px solid #ccc;display:flex;align-items:center;justify-content:center}
.gallery-title{left:186px;top:895px;font-family:"Roboto Slab",Georgia,serif;font-size:16px;color:#222}
.g-arrow{top:897px;width:14px;height:14px;display:flex;align-items:center;justify-content:center}
.thumb{top:933px;width:120px;height:95px;border:3px solid #fff;outline:1px solid #888}

/* footer */
.footer{left:0;top:1042px;width:930px;height:132px;background:var(--footer);color:#ddd;font-size:9.2px}
.f-head{font-size:9.6px;font-weight:700;color:#fff;padding-bottom:3px;border-bottom:1px dashed #777;display:inline-block}
.f-list{list-style:none;line-height:15.5px;margin-top:8px}
.f-row{display:flex;gap:12px;line-height:13px}
.f-row b{width:10px;color:#fff}
.f-time{display:flex;gap:6px;align-items:center;height:22px}
.f-brand{font-family:"Roboto Slab",Georgia,serif;font-size:13px;color:#ddd;letter-spacing:1px;display:flex;align-items:center;gap:5px}
.f-brand i{width:14px;height:14px;background:#ddd;display:block}
.cards{display:flex;gap:3px;margin-top:6px}
.cards span{width:21px;height:14px;border-radius:2px;display:block}
.bottom{left:0;top:1174px;width:930px;height:26px;background:var(--blue);color:#fff;font-size:9px;text-align:center;line-height:26px}
</style>
</head>
<body>
<div class="page">

  <header>
    <div class="abs brand"><span class="brand-mark"></span><span class="brand-name">BLUEFINCH PAINTING</span></div>
    <div class="abs trailer" role="img" aria-label="Company trailer with branding"></div>
    <div class="abs estimate-btn">Free Estimates</div>
    <div class="abs call">
      <svg width="22" height="22" viewBox="0 0 22 22"><circle cx="11" cy="11" r="10" fill="none" stroke="#1e7cc8" stroke-width="1.3"/><path d="M8 6c-1 2-1 5 1 8s4 4 5 3l1-1-2-2-1 1c-1 0-3-3-3-4l1-1-1-3z" fill="#1e7cc8"/></svg>
      <div><small>Call Us Today</small><strong>555-318-7046</strong></div>
    </div>
  </header>

  <nav class="abs nav">
    <a class="active" style="width:57px">Home</a>
    <a style="width:91px">About Us</a>
    <a style="width:80px">Exterior</a>
    <a style="width:78px">Interior</a>
    <a style="width:97px">Residential</a>
    <a style="width:102px">Commerical</a>
    <a style="width:104px">Past Projects</a>
    <a style="width:95px">Contact Us</a>
  </nav>

  <section class="abs hero" role="img" aria-label="Painter on a ladder sponging a yellow interior wall">
    <div class="abs hero-arrow" style="left:87px;top:106px"><svg width="10" height="12"><path d="M7 1L2 6l5 5" stroke="#fff" fill="none" stroke-width="1.5"/></svg></div>
    <div class="abs hero-arrow" style="left:812px;top:106px"><svg width="10" height="12"><path d="M3 1l5 5-5 5" stroke="#fff" fill="none" stroke-width="1.5"/></svg></div>
  </section>
  <div class="abs hero-copy">
    <div class="hero-brand"><i></i>BLUEFINCH PAINTING</div>
    <div class="hero-tag">PROVIDING QUALITY<br>WORK AT<br>AFFORDABLE PRICES</div>
  </div>

  <section class="abs welcome">
    <h1>Welcome to Bluefinch Painting</h1>
    <svg width="270" height="14" style="margin-top:4px"><line x1="2" y1="4" x2="268" y2="4" stroke="#fff"/><line x1="2" y1="7" x2="268" y2="7" stroke="#fff"/><path d="M130 3l10 8M140 3l-10 8" stroke="#fff"/></svg>
    <p>Lorem ipsum dolor sit amet, consectetuer adipiscing elit, sed diam nonummy nibh euismod&nbsp; rent ut laoreet dolore magna aliquam erat volutpat. Ut wisi enim ad minim veniam, quis nostrud lore xererci tation ullamcorper suscipit lobortis nisl ut aliquip ex ea commodo consequat. Duis autem revel eum iriure dolor in hendrerit in vulputate velit esse molestie consequat.</p>
    <div style="position:relative;margin-top:12px;height:18px">
      <svg class="abs" style="left:369px;top:0" width="192" height="18"><line x1="0" y1="9" x2="192" y2="9" stroke="#fff"/><line x1="54" y1="6" x2="138" y2="6" stroke="#fff"/><line x1="54" y1="12" x2="138" y2="12" stroke="#fff"/></svg>
      <span class="read-dark" style="position:relative">Read More</span>
    </div>
  </section>

  <h2 class="abs col-title" style="left:133px;top:602px">Residential Painting</h2>
  <div class="abs photo" style="left:134px;top:633px;width:206px;height:130px;background:linear-gradient(135deg,#5a5049,#b69a78 55%,#e9e4dc)" role="img" aria-label="Freshly painted living room interior"></div>
  <p class="abs col-text" style="left:134px;top:770px">Sed ut perspiciatis unde omnis iste natus error sit voluptatem accusantium doloremque laudantium, totam rem aperiam.</p>
  <span class="abs read-dark" style="left:134px;top:819px">Read More</span>

  <h2 class="abs col-title" style="left:370px;top:602px">Commerical Painting</h2>
  <div class="abs photo" style="left:371px;top:633px;width:206px;height:130px;background:linear-gradient(90deg,#e6e5dc,#f1f0e8 70%,#1a2a44 92%)" role="img" aria-label="Painter rolling a white commercial wall"></div>
  <p class="abs col-text" style="left:373px;top:770px">Sed ut perspiciatis unde omnis iste natus error sit voluptatem accusantium doloremque laudantium, totam rem aperiam.</p>
  <span class="abs read-dark" style="left:373px;top:819px">Read More</span>

  <h2 class="abs col-title" style="left:608px;top:602px">Quick Inquiry</h2>
  <div class="abs inquiry-rule"></div>
  <div class="abs field" style="top:637px">Name</div>
  <div class="abs field" style="top:665px">Email</div>
  <div class="abs field" style="top:694px">Phone</div>
  <div class="abs field" style="top:723px">Type of Work</div>
  <div class="abs field" style="top:753px;height:58px">Message</div>
  <div class="abs submit">Submit</div>

  <div class="abs divider"></div>
  <div class="abs gallery-icon"><svg width="20" height="18"><rect x="1" y="4" width="13" height="13" fill="none" stroke="#444" stroke-width="1.6"/><rect x="5" y="1" width="13" height="13" fill="#fff" stroke="#444" stroke-width="1.6"/><rect x="8" y="5" width="7" height="6" fill="#444"/></svg></div>
  <div class="abs gallery-title">Our Work Gallery</div>
  <div class="abs g-arrow" style="left:771px;background:#111"><svg width="8" height="8"><path d="M6 1L2 4l4 3" stroke="#fff" fill="none" stroke-width="1.6"/></svg></div>
  <div class="abs g-arrow" style="left:787px;background:var(--blue)"><svg width="8" height="8"><path d="M2 1l4 3-4 3" stroke="#fff" fill="none" stroke-width="1.6"/></svg></div>

  <div class="abs thumb" style="left:138px;background:linear-gradient(#e4d6bc,#a8744a)" role="img" aria-label="Entry hall with staircase and wood floor"></div>
  <div class="abs thumb" style="left:272px;background:linear-gradient(#2a66b2,#c7d0dc 55%,#e8eaee)" role="img" aria-label="Painter working on a white house exterior"></div>
  <div class="abs thumb" style="left:406px;background:linear-gradient(90deg,#e3c57a,#e9cd58,#d8c7a7)" role="img" aria-label="Yellow hallway with built-in shelving"></div>
  <div class="abs thumb" style="left:540px;background:linear-gradient(#a6bfdc,#c2b49c 50%,#4f8a3a)" role="img" aria-label="Two-storey house with palm trees and lawn"></div>
  <div class="abs thumb" style="left:674px;background:linear-gradient(90deg,#d9d3c4,#f0ece2,#c7a575)" role="img" aria-label="White staircase with potted plant"></div>

  <footer class="abs footer">
    <div class="abs" style="left:133px;top:19px">
      <span class="f-head">Quick Links</span>
      <ul class="f-list">
        <li>• Home</li><li>• About Us</li><li>• Services</li><li>• Past Projects</li><li>• Contact Us</li>
      </ul>
    </div>
    <div class="abs" style="left:290px;top:19px">
      <span class="f-head">Contact Information</span>
      <div class="f-row" style="margin-top:7px"><b>A:</b><span>Bluefinch Painting<br>Street Name City Name<br>State Zipcode</span></div>
      <div class="f-row" style="margin-top:9px"><b>P:</b><span>555-318-7046</span></div>
      <div class="f-row" style="margin-top:6px"><b>E:</b><span>inquiry@bluefinchpainting.example</span></div>
    </div>
    <div class="abs" style="left:472px;top:19px">
      <span class="f-head" style="width:111px">Work Times</span>
      <div style="margin-top:3px">
        <div class="f-time"><svg width="11" height="11"><rect x="1" y="3" width="9" height="7" fill="#ddd"/><rect x="3" y="1" width="5" height="3" fill="#ddd"/></svg>Our work timings are:</div>
        <div class="f-time"><svg width="11" height="11"><circle cx="5.5" cy="5.5" r="4.5" fill="none" stroke="#ddd"/><path d="M5.5 3v3h2" stroke="#ddd" fill="none"/></svg>Monday - Friday. 8AM - 8PM</div>
        <div class="f-time"><svg width="11" height="11"><circle cx="5.5" cy="5.5" r="4.5" fill="none" stroke="#ddd"/><path d="M5.5 3v3h2" stroke="#ddd" fill="none"/></svg>Saturday:9AM - 4PM</div>
        <div class="f-time"><svg width="11" height="11"><circle cx="5.5" cy="5.5" r="4.5" fill="none" stroke="#ddd"/><path d="M3.5 7.5l4-4" stroke="#ddd"/></svg>Sunday: closed</div>
      </div>
    </div>
    <div class="abs" style="left:658px;top:26px;width:140px;text-align:center">
      <div class="f-brand"><i></i>BLUEFINCH PAINTING</div>
      <div style="margin-top:16px;color:#fff">We Accept</div>
      <div class="cards" style="justify-content:center">
        <span style="background:#2d5fb0"></span><span style="background:#eee"></span><span style="background:#e9e9e9"></span><span style="background:#5aa0d8"></span><span style="background:#d9463a"></span>
      </div>
    </div>
  </footer>
  <div class="abs bottom">Copyright ©2015, BluefinchPainting&nbsp; All Rights Reserved</div>

</div>
</body>
</html>
```